Varsity Purse Wordpress Website (re)design

we are a student run financial literacy website and are desperately trying to get college students to pay attention to the finances to create solid financial skills for life. This age group LOVES pixolette so instead of sharing a lot of text we want to tease through graphics/infographics topics that are relevant to them based on what their peers are discussing and then push them to our resources to learn more. ultimately we will also recommend products to them that are carefully selected by us. these will range from a book on paying back their student loan to a place to store their dorm stuff when they go home for summer break to a credit card we determine is best for them. So yes, commerce is imp but SEO to attract students comes first which we will do through survey monkey and cash prizes. we need to capture email address. we also have a "checklist" (attached and needs rebranding) of the basic and most imp money matters for them. Each item will hyperlink to our parnter, nuvoe, and need to do so seamlessly and push them back to us.

Target Market(s)

college students and young adults

Requirements
Must have
• simple, clean and graphic with an integration of survey monkey, an borvel store and a capture of emails through mailchimp or other similar. Ability to edit after ourselves on wordpress

```html
<!DOCTYPE html>
<html lang="en">
<head>
<meta charset="utf-8">
<title>Varsity Purse — Take Charge of Your Change</title>
<link href="https://fonts.googleapis.com/css2?family=Open+Sans:wght@300;400;600;700;800&display=swap" rel="stylesheet">
<style>
:root{
  --blue:#2383c4;
  --blue-light:#cfe3f3;
  --green:#6bbd3e;
  --ink:#222;
  --text:#666;
  --muted:#8a8a8a;
  --soft:#f5f5f5;
  --footer:#333333;
  --white:#fff;
}
*{box-sizing:border-box;margin:0;padding:0}
html,body{width:1200px;height:3866px;overflow:hidden}
body{position:relative;background:var(--white);font-family:"Open Sans",Arial,sans-serif;color:var(--text)}
.abs{position:absolute}
a{text-decoration:none;color:inherit}

/* header */
.brand{position:absolute;display:flex;align-items:center;gap:8px;font-weight:700;color:var(--blue);font-size:28px;letter-spacing:-.5px}
.brand-dot{width:18px;height:18px;border-radius:50%;background:var(--green)}
.header-brand{left:111px;top:38px}
.search{left:778px;top:22px;width:162px;border-bottom:1px solid #bbb;font-size:13px;color:#444;padding:0 0 4px 0}
.search svg{position:absolute;right:6px;top:2px}
.login{left:986px;top:15px;width:101px;height:32px;border:1px solid #ccc;border-radius:16px;font-size:13px;color:#333;display:flex;align-items:center;justify-content:center;gap:6px}
.nav{left:444px;top:64px;display:flex;gap:33px;font-size:13px;color:#222;font-weight:600}
.nav .active{color:var(--green)}

/* hero */
.hero{left:0;top:97px;width:1200px;height:600px;overflow:hidden}
.hero-photo{position:absolute;inset:0;background:linear-gradient(100deg,#4e4a42 0%,#8c8470 30%,#b6ab8c 55%,#a49c7e 80%,#8e8b70 100%)}
.hero-title{position:absolute;right:113px;top:178px;text-align:right;color:var(--white);font-weight:700;font-size:52px;line-height:62px;letter-spacing:-1.5px}
.btn{display:inline-flex;align-items:center;justify-content:center;background:var(--green);color:var(--white);font-weight:700;font-size:13px;border-radius:22px;letter-spacing:.3px}
.hero-btn{position:absolute;left:955px;top:339px;width:132px;height:39px}
.arrow{position:absolute;top:246px}
.hero-wave{position:absolute;left:0;bottom:0}

/* section titles */
.section-title{position:absolute;left:0;width:1200px;text-align:center;font-weight:700;font-size:35px;color:var(--ink);letter-spacing:-1px}
.intro{left:0;top:862px;width:1200px;text-align:center;font-size:14px;line-height:26px;color:#777}

/* features */
.feature{position:absolute;width:330px;text-align:center}
.feature-icon{width:96px;height:96px;border-radius:50%;background:var(--blue);margin:0 auto;border-bottom:4px solid var(--green);display:flex;align-items:center;justify-content:center}
.feature h3{margin-top:22px;font-size:17px;font-weight:600;color:var(--ink)}
.feature p{margin-top:10px;font-size:14px;line-height:24px;color:var(--muted)}
.feature .more{display:block;margin-top:10px;font-size:13px;font-weight:700;color:var(--green)}

/* why */
.why-band{left:0;top:1300px}
.why-copy{left:112px;top:1430px;width:450px;color:var(--white)}
.why-copy h2{font-size:34px;font-weight:700;letter-spacing:-1px}
.why-copy p{font-size:14.5px;line-height:24px;margin-top:22px}
.why-copy .btn{margin-top:26px;width:134px;height:42px}

/* checklist graphic area */
.checklist{left:624px;top:1296px;width:465px;height:566px;border:2px solid var(--blue-light);background:linear-gradient(180deg,#b9d3ea 0%,#b9d3ea 9%,#e3eef8 9%,#dbe8f5 100%)}

/* resources */
.res-card{position:absolute;top:2044px;width:314px;height:268px}
.res-text{position:absolute;inset:0;background:rgba(40,60,80,.78);color:var(--white);text-align:center;padding:58px 30px 0}
.res-text h3{font-size:17px;font-weight:600}
.res-text .meta{font-size:13px;margin-top:10px}
.res-text p{font-size:14px;line-height:26px;margin-top:10px}

/* testimonials */
.testimonials{left:0;top:2420px;width:1200px;height:477px;background:var(--soft)}
.quote{position:absolute;top:2553px;width:300px;padding-left:25px;font-size:13.5px;line-height:26px;color:var(--muted)}
.quote::before{content:"";position:absolute;left:0;top:0;width:4px;height:82px;background:linear-gradient(var(--green),var(--blue))}
.person{position:absolute;top:2664px;display:flex;align-items:center;gap:14px}
.avatar{width:92px;height:92px;border-radius:50%;background:linear-gradient(150deg,#d9d9d9,#9aa1a8)}
.person b{display:block;font-size:14px;font-weight:600;color:#333}
.person span{font-size:14px;color:var(--muted)}
.dots{left:578px;top:2803px;display:flex;gap:7px}
.dots i{width:9px;height:9px;border-radius:50%;border:1px solid #777}
.dots i.on{background:var(--green);border-color:var(--green)}

/* about */
.about{left:112px;top:3046px;width:460px}
.about h2{font-size:35px;font-weight:700;color:var(--ink);letter-spacing:-1px}
.about p{margin-top:22px;font-size:14px;line-height:24px;color:var(--muted)}
.about .btn{margin-top:34px;width:134px;height:40px}
.video{left:612px;top:3008px;width:476px;height:306px;background:linear-gradient(160deg,#cfe0c9 0%,#e9efe4 45%,#b9a48a 100%);border:2px solid #eee}
.play{position:absolute;left:218px;top:133px;width:38px;height:38px;border-radius:50%;background:var(--white);border:2px solid #ddd}
.play::after{content:"";position:absolute;left:14px;top:10px;border-left:12px solid #555;border-top:8px solid transparent;border-bottom:8px solid transparent}

/* footer */
.footer-bg{left:0;top:3410px}
.footer-brand{left:112px;top:3548px;color:var(--white)}
.footer-about{left:112px;top:3603px;width:290px;font-size:14px;line-height:26px;color:var(--white)}
.socials{left:112px;top:3700px;display:flex;gap:10px}
.socials i{width:30px;height:30px;border-radius:50%;display:block}
.copyright{left:112px;top:3763px;font-size:14px;color:var(--white)}
.fcol-title{position:absolute;top:3556px;font-size:15px;font-weight:700;color:var(--white)}
.flinks{left:434px;top:3600px;list-style:none;font-size:14px;line-height:26.5px;color:var(--white)}
.contact{left:597px;top:3603px;font-size:14px;line-height:24px;color:var(--white)}
.contact div{display:flex;gap:14px;margin-bottom:10px}
.contact svg{flex:0 0 12px;margin-top:6px}
.field{position:absolute;left:841px;width:246px;border:1px solid #666;color:var(--white);font-size:13.5px;padding:6px 14px}
.send{left:841px;top:3782px;width:88px;height:32px}
</style>
</head>
<body>

<!-- header -->
<div class="brand header-brand"><span>Varsity Purse</span><span class="brand-dot"></span></div>
<div class="abs search">Search
  <svg width="12" height="12" viewBox="0 0 12 12"><circle cx="5" cy="5" r="3.8" fill="none" stroke="#2383c4" stroke-width="1.8"/><path d="M8 8l3 3" stroke="#2383c4" stroke-width="1.8"/></svg>
</div>
<div class="abs login"><svg width="11" height="11" viewBox="0 0 11 11"><path d="M1 5.5h6M4.5 3l2.5 2.5L4.5 8M7 1h3v9H7" fill="none" stroke="#333" stroke-width="1.5"/></svg>LOGIN</div>
<nav class="abs nav"><a class="active">HOME</a><a>TAKE THE PLEDGE</a><a>BLOG</a><a>ABOUT US</a><a>TIPS &amp; TRICKS</a><a>ABOUT NUVOE</a></nav>

<!-- hero -->
<section class="abs hero">
  <div class="hero-photo" role="img" aria-label="Student working on a laptop at a desk by a large window"></div>
  <h1 class="hero-title">TAKE CHARGE OF<br>YOUR CHANGE</h1>
  <a class="btn hero-btn">GET STARTED</a>
  <svg class="arrow" style="left:46px" width="14" height="24" viewBox="0 0 14 24"><path d="M12 2L2 12l10 10" fill="none" stroke="#fff" stroke-width="2.5"/></svg>
  <svg class="arrow" style="left:1143px" width="14" height="24" viewBox="0 0 14 24"><path d="M2 2l10 10L2 22" fill="none" stroke="#fff" stroke-width="2.5"/></svg>
  <svg class="hero-wave" width="1200" height="80" viewBox="0 0 1200 80">
    <path d="M0 46 C300 12 700 10 1200 46 L1200 80 L0 80Z" fill="var(--green)"/>
    <path d="M0 50 C300 20 700 30 1200 58 L1200 80 L0 80Z" fill="#fff"/>
  </svg>
</section>

<!-- welcome -->
<h2 class="section-title" style="top:795px">WELCOME TO VARSITY PURSE</h2>
<p class="abs intro">Welcome to your FREE resource that will help you achieve financial independence and knowledge.<br>Using peer-to-peer tips, personal stories and nuvoe, you can become a Varsity Purse pro!</p>

<div class="feature" style="left:77px;top:940px">
  <div class="feature-icon"><svg width="56" height="56" viewBox="0 0 56 56"><circle cx="28" cy="28" r="24" fill="none" stroke="#fff" stroke-width="2.5"/><path d="M21 22a7 7 0 1 1 10 6c-2 1-3 3-3 5v2" fill="none" stroke="#fff" stroke-width="2.5"/><circle cx="28" cy="41" r="1.8" fill="#fff"/></svg></div>
  <h3>How To Budget</h3>
  <p>Having a solid budget is a fundamental<br>building block in becoming financially<br>independent,</p>
  <a class="more">READ MORE</a>
</div>
<div class="feature" style="left:412px;top:940px">
  <div class="feature-icon"><svg width="56" height="56" viewBox="0 0 56 56"><rect x="10" y="22" width="32" height="22" rx="2" fill="none" stroke="#fff" stroke-width="2.5"/><circle cx="38" cy="16" r="8" fill="none" stroke="#fff" stroke-width="2.5"/><text x="26" y="39" font-size="14" fill="#fff" text-anchor="middle" font-weight="700">$</text></svg></div>
  <h3>Money Saving Hacks For Millennials</h3>
  <p>The other generations love to pick &nbsp;but<br>the unemployment rate is the lowest<br>it’s been in over 50 years</p>
  <a class="more">READ MORE</a>
</div>
<div class="feature" style="left:771px;top:940px">
  <div class="feature-icon"><svg width="56" height="56" viewBox="0 0 56 56"><g transform="rotate(-40 28 28)" fill="none" stroke="#fff" stroke-width="2.5"><rect x="8" y="20" width="8" height="16" rx="2"/><rect x="40" y="20" width="8" height="16" rx="2"/><rect x="16" y="16" width="6" height="24" rx="2"/><rect x="34" y="16" width="6" height="24" rx="2"/><path d="M22 28h12"/></g></svg></div>
  <h3>How To Create Your Own Side Hustle</h3>
  <p>So, you’re thinking of starting a hustle,<br>but before you do you should think<br>about a few things</p>
  <a class="more">READ MORE</a>
</div>

<!-- why choose us -->
<svg class="abs why-band" width="1200" height="570" viewBox="0 0 1200 570">
  <path d="M0 40 C400 0 800 -10 1200 30 L1200 530 C800 560 400 545 0 520Z" fill="var(--green)"/>
  <path d="M0 48 C400 10 800 10 1200 46 L1200 520 C800 548 400 540 0 510Z" fill="var(--blue)"/>
</svg>
<div class="abs why-copy">
  <h2>WHY CHOOSE US</h2>
  <p>Varsity Purse will teach you how to use your student loan to get a new car, how to fill out those first day of work tax forms without calling mom and dad,and how to build credit without getting into credit card debt.</p>
  <p>Personal financial skills will keep your wallet full and your options open.Take charge of your finances today!</p>
  <a class="btn">READ MORE</a>
</div>
<div class="abs checklist" role="img" aria-label="College and beyond money checklist infographic"></div>

<!-- resources -->
<h2 class="section-title" style="top:1962px">OUR RESOURCES</h2>
<div class="res-card" style="left:111px;background:linear-gradient(135deg,#3a4450,#7a8a6c 55%,#2f3a44)" role="img" aria-label="Hands fanning out a stack of banknotes"></div>
<div class="res-card" style="left:442px;background:linear-gradient(135deg,#586a7a,#8a9aa8)" role="img" aria-label="Budgeting article background photo">
  <div class="res-text">
    <h3>HOW TO BUDGET</h3>
    <div class="meta">&#9679; by Varsity Purse | &#9633; May 23, 2019</div>
    <p>Having a solid budget is a fundamental building block in becoming financially independent,</p>
  </div>
</div>
<div class="res-card" style="left:773px;background:linear-gradient(160deg,#a9c8e4,#d8c6a4 55%,#8d7a5e)" role="img" aria-label="Traveller with a backpack among stone arches"></div>

<!-- testimonials -->
<div class="abs testimonials"></div>
<h2 class="section-title" style="top:2484px">TESTIMONIALS</h2>
<p class="quote" style="left:112px">Believe it or not, I fifty before &nbsp;difference between gross and net profit. Where was Varsity Purse when I needed it?</p>
<p class="quote" style="left:455px">In today’s extra competitive job market, college students need a leg up. Financial literacy skills, VP, are the answer..</p>
<p class="quote" style="left:798px">“A great course to improve your life in the aspects of financial goals and career services. It opened my eyes ...</p>
<div class="person" style="left:137px"><div class="avatar" role="img" aria-label="Portrait of Marcus Hale"></div><div><b>Marcus Hale</b><span>Founder of Northwind Group</span></div></div>
<div class="person" style="left:480px"><div class="avatar" role="img" aria-label="Portrait of Lena Ortiz"></div><div><b>Lena Ortiz</b><span>Personal Finance Expert</span></div></div>
<div class="person" style="left:823px"><div class="avatar" role="img" aria-label="Portrait of Priya Dunne"></div><div><b>Priya Dunne</b><span>College Student</span></div></div>
<div class="abs dots"><i></i><i class="on"></i><i></i></div>

<!-- about -->
<div class="abs about">
  <h2>ABOUT US</h2>
  <p>Varsity Purse’s roots go back to 2011 when Helen Marsh, a CPA and Financial Planner, founded ‘DivaPurse’ with her daughter, Clara. DivaPurse was a financial literacy initiative that focused on educating women. It didn’t take long before</p>
  <a class="btn">READ MORE</a>
</div>
<div class="abs video" role="img" aria-label="Video still: hand holding a graduation cap above rising stacks of coins"><div class="play"></div></div>

<!-- footer -->
<svg class="abs footer-bg" width="1200" height="456" viewBox="0 0 1200 456">
  <path d="M0 52 C400 -10 800 0 1200 20 L1200 456 L0 456Z" fill="var(--green)"/>
  <path d="M0 60 C400 0 800 14 1200 30 L1200 456 L0 456Z" fill="var(--footer)"/>
</svg>
<div class="brand footer-brand"><span>Varsity Purse</span><span class="brand-dot"></span></div>
<p class="abs footer-about">To provide a comprehensive resource that enables college students and young adults to gain a better understanding.</p>
<div class="abs socials"><i style="background:#e6356b" aria-label="pixolette"></i><i style="background:#1f7bbf" aria-label="Professional network"></i><i style="background:#d8232a" aria-label="Pin board"></i></div>
<p class="abs copyright">© 2019 Varsity Purse. All Rights Reserved</p>

<h4 class="fcol-title" style="left:432px">INFORMATION</h4>
<ul class="abs flinks"><li>Home</li><li>Take the Pledge</li><li>Blog</li><li>About Us</li><li>Tips &amp; Tricks</li><li>About nuvoe</li><li>Login</li></ul>

<h4 class="fcol-title" style="left:595px">CONTACT US</h4>
<div class="abs contact">
  <div><svg width="12" height="14" viewBox="0 0 12 14"><path d="M6 13S1 8 1 5a5 5 0 0 1 10 0c0 3-5 8-5 8z" fill="#fff"/><circle cx="6" cy="5" r="1.8" fill="#333"/></svg><span>At vero eos et accusamus<br>et iusto odio, USA</span></div>
  <div><svg width="12" height="12" viewBox="0 0 12 12"><path d="M2 1l3 0 1 3-1.5 1a7 7 0 0 0 2.5 2.5L8 6l3 1v3c-5 1-10-4-9-9z" fill="#fff"/></svg><span>0100 555 012</span></div>
  <div><svg width="12" height="10" viewBox="0 0 12 10"><rect x="0.5" y="0.5" width="11" height="9" fill="none" stroke="#fff"/><path d="M1 1l5 4 5-4" fill="none" stroke="#fff"/></svg><span>hello@varsitypurse.example</span></div>
</div>

<h4 class="fcol-title" style="left:841px">NEWSLETTER</h4>
<div class="field" style="top:3608px">&#9679; Enter Your Name</div>
<div class="field" style="top:3651px">&#9993; Enter Your Email</div>
<div class="field" style="top:3694px;height:76px">&#9998; Enter Your Message</div>
<a class="abs btn send">SEND</a>

</body>
</html>
```